Volunteer fire fighters needed banner

As part of our recruitment campaign, we need a sign we can post on our sign trailer to entice locals to join our volunteer fire service. This design will be printed on a banner, front and back, to catch traffic going in both directions on a busy roadway. This banner will have a printed surface of 4 feet tall by 8 feet long.
Our fire department is looking to attract people between the ages of 18 and 35 years old who are interested in being a firefighter. We offer our volunteers:
-Free professional training
-All equipment supplied
-Tax abatements for active volunteers
For more information, you can check us out at:
Brackenmoorfire.example

This design should:
-scale to and fit a 4'x8' canvas
-Include our web address "BrackenMoorFire.example"
-Say "Members Wanted"
-"Drill every Tuesday at 7pm"
-"57 Kestrel Pond Lane"
-Include "Bracken Moor Fire Department"

We've included reference photos and past images we use for our other campaigns for inspiration for you.

Target Market(s)

18-35 y/o

Industry/Entity Type

Fire Service

Requirements
Must have
• -scale to and fit a 4'x8' canvas -Include our web address "BrackenMoorFire.example" -Say "Members Wanted" -"Drill every Tuesday at 7pm" -"57 Kestrel Pond Lane" -Include "Bracken Moor Fire Department"

```html
<!DOCTYPE html>
<html lang="en">
<head>
<meta charset="utf-8">
<title>Members Wanted – Bracken Moor Fire Department</title>
<link rel="stylesheet" href="https://fonts.googleapis.com/css2?family=Anton&family=Montserrat:wght@600;700;800&family=Oswald:wght@600&display=swap">
<style>
  :root {
    --backdrop: #2d2d2d;
    --paper: #eeecec;
    --navy: #333d72;
    --gold: #fbb21c;
    --red: #e3000f;
    --headline-red: #c8000c;
    --ink: #2b2b2b;
    --white: #ffffff;
  }
  * { margin: 0; padding: 0; box-sizing: border-box; }
  html, body { width: 1200px; height: 1200px; overflow: hidden; background: var(--backdrop); }
  .canvas { position: relative; width: 1200px; height: 1200px; background: var(--backdrop); }
  .banner { position: absolute; left: 0; top: 300px; width: 1200px; height: 600px; background: var(--paper); overflow: hidden; font-family: 'Montserrat', sans-serif; }
  .bands, .photo-grid { position: absolute; inset: 0; }
  .dept-name {
    position: absolute; left: 20px; top: 40px; width: 160px;
    display: flex; flex-direction: column; align-items: center; gap: 10px;
    color: var(--white); font-weight: 800; font-size: 19px; line-height: 1.2; text-align: center; text-transform: uppercase;
  }
  .dept-name .dot { width: 34px; height: 34px; border-radius: 50%; background: var(--red); }
  .headline {
    position: absolute; left: 190px; top: 60px; white-space: nowrap;
    font-family: 'Anton', sans-serif; font-size: 74px; line-height: 1; letter-spacing: -1px;
    color: var(--headline-red); text-transform: uppercase;
    transform: scaleX(0.88); transform-origin: left center;
    text-shadow: 2px 2px 0 var(--white), -2px -2px 0 var(--white), 2px -2px 0 var(--white), -2px 2px 0 var(--white), 4px 5px 6px rgba(0,0,0,.45);
  }
  .intro { position: absolute; left: 42px; top: 214px; width: 735px; font-weight: 600; font-size: 20.5px; line-height: 1.22; color: var(--ink); }
  .offer-tag { position: absolute; left: 41px; top: 270px; width: 389px; height: 37px; background: var(--red); color: var(--white); font-weight: 800; font-size: 19.5px; line-height: 37px; padding-left: 21px; text-transform: uppercase; }
  .benefits { position: absolute; left: 40px; top: 310px; list-style: none; }
  .benefits li { display: flex; align-items: center; gap: 9px; height: 29px; font-weight: 800; font-size: 21px; color: var(--ink); text-transform: uppercase; letter-spacing: .3px; white-space: nowrap; }
  .benefits svg { width: 19px; height: 20px; }
  .drill { position: absolute; left: 39px; top: 403px; font-weight: 700; font-size: 29px; color: var(--red); white-space: nowrap; }
  .drill .time { color: var(--navy); }
  .address { position: absolute; left: 38px; top: 440px; display: flex; align-items: center; gap: 8px; font-weight: 600; font-size: 21px; color: var(--ink); white-space: nowrap; }
  .more-info {
    position: absolute; left: 27px; top: 484px; white-space: nowrap;
    font-family: 'Oswald', sans-serif; font-weight: 600; font-size: 25px; color: var(--ink); text-transform: uppercase; letter-spacing: -.3px;
    transform: scaleX(0.84); transform-origin: left center;
  }
  .web { position: absolute; left: 27px; top: 544px; font-weight: 700; font-size: 29px; color: var(--white); white-space: nowrap; }
  .event-art { position: absolute; left: 533px; top: 402px; width: 128px; height: 190px; border-radius: 50% 50% 30% 30%; background: radial-gradient(circle at 50% 45%, #ffffff 0 30%, #f3c44a 31% 55%, #e53a2e 56% 100%); }
  .corner-name { position: absolute; left: 1020px; top: 22px; width: 165px; display: flex; align-items: center; gap: 8px; color: var(--white); font-weight: 800; font-size: 15px; line-height: 1.15; text-transform: uppercase; }
  .corner-name .dot { flex: 0 0 22px; height: 22px; border-radius: 50%; background: var(--white); }
</style>
</head>
<body>
<div class="canvas">
  <section class="banner">
    <svg class="bands" viewBox="0 0 1200 600" aria-hidden="true">
      <polygon points="0,17 596,17 752,186 0,186" fill="var(--navy)"/>
      <polygon points="175,31 610,31 735,168 175,168" fill="var(--gold)"/>
      <polygon points="0,477 490,477 531,529 0,529" fill="var(--gold)"/>
      <polygon points="0,529 832,529 832,600 0,600" fill="var(--navy)"/>
    </svg>

    <svg class="photo-grid" viewBox="0 0 1200 600">
      <defs>
        <linearGradient id="gTraining" x1="0" y1="0" x2="1" y2="1"><stop offset="0" stop-color="#b7a893"/><stop offset=".5" stop-color="#6b5438"/><stop offset="1" stop-color="#d8d23a"/></linearGradient>
        <linearGradient id="gTruck" x1="0" y1="0" x2="1" y2="1"><stop offset="0" stop-color="#cfd3d6"/><stop offset=".45" stop-color="#d4141c"/><stop offset="1" stop-color="#6e6e6a"/></linearGradient>
        <linearGradient id="gScene" x1="0" y1="0" x2="1" y2="1"><stop offset="0" stop-color="#2c2a28"/><stop offset=".6" stop-color="#7a5a36"/><stop offset="1" stop-color="#3b3a38"/></linearGradient>
        <linearGradient id="gPortrait" x1="0" y1="0" x2="0" y2="1"><stop offset="0" stop-color="#a8d2ef"/><stop offset="1" stop-color="#4c4640"/></linearGradient>
        <linearGradient id="gEngine" x1="0" y1="0" x2="1" y2="1"><stop offset="0" stop-color="#c9101a"/><stop offset="1" stop-color="#505050"/></linearGradient>
      </defs>
      <g stroke="var(--white)" stroke-width="6" stroke-linejoin="round">
        <polygon role="img" aria-label="Firefighter in turnout gear and helmet during training" points="578,0 1000,0 810,197 775,197" fill="url(#gTraining)"/>
        <polygon role="img" aria-label="Red fire department tanker truck in the station bay" points="1000,0 1200,0 1200,405 1115,490 807,215" fill="url(#gTruck)"/>
        <polygon role="img" aria-label="Firefighters working a hose line at a fire scene" points="674,414 832,268 981,420 832,576" fill="url(#gScene)"/>
        <polygon role="img" aria-label="Firefighter wearing breathing apparatus mask" points="842,600 969,436 1149,600" fill="url(#gPortrait)"/>
        <polygon role="img" aria-label="Front of a red fire engine" points="1200,405 1200,600 1185,600 1100,507" fill="url(#gEngine)"/>
      </g>
    </svg>

    <div class="dept-name"><span class="dot"></span>Bracken Moor Fire Department</div>
    <div class="corner-name"><span class="dot"></span>Bracken Moor Fire Department</div>

    <h1 class="headline">Members Wanted</h1>

    <p class="intro">Our fire department is looking to attract people between the ages of 18 and 35 years old who are interested in being a firefighter.</p>

    <div class="offer-tag">We offer our volunteers:</div>
    <ul class="benefits">
      <li><svg viewBox="0 0 19 20"><path d="M1 11 L7 18 L18 1" fill="none" stroke="var(--red)" stroke-width="3"/></svg>Free professional training</li>
      <li><svg viewBox="0 0 19 20"><path d="M1 11 L7 18 L18 1" fill="none" stroke="var(--red)" stroke-width="3"/></svg>All equipment supplied</li>
      <li><svg viewBox="0 0 19 20"><path d="M1 11 L7 18 L18 1" fill="none" stroke="var(--red)" stroke-width="3"/></svg>Tax abatements for active volunteers</li>
    </ul>

    <p class="drill">Drill every Tuesday at <span class="time">7pm</span></p>
    <p class="address">
      <svg width="20" height="28" viewBox="0 0 20 28" aria-hidden="true"><path d="M10 1 C4.5 1 1 5 1 9.5 C1 15 10 22 10 22 C10 22 19 15 19 9.5 C19 5 15.5 1 10 1 Z" fill="var(--red)"/><circle cx="10" cy="9.5" r="3.2" fill="var(--white)"/><ellipse cx="10" cy="25" rx="7" ry="2" fill="none" stroke="var(--ink)" stroke-width="1.6"/></svg>
      57 Kestrel Pond Lane
    </p>

    <p class="more-info">For more information, you can check us out at:</p>
    <p class="web">www.BrackenMoorFire.example</p>

    <div class="event-art" role="img" aria-label="Community egg hunt event artwork with a cartoon mascot"></div>
  </section>
</div>
</body>
</html>
```